Buch-/eBook-Cover für Traumatherapeutin
Zielgruppe
Ich bin Traumatherapeutin und schreibe ein Buch zum Thema Trauma bearbeiten.
Meine Zielgruppe sucht Heilung, Genesung, Selbstliebe etc.
Aufgabenstellung
Buchcover
Bitte erstell mir ein modernes positives inspirierendes Buchcover mit dem
Titel: 'Morgenlicht NEU entdecken“
Untertitel: „Spüre den Mut der ganz in dir wohnt“
Dr. Mira Kessow
Ich hätte gerne ein modernes Buch, das entweder einen Bezug zum Thema Trauma hat oder aber einfach stylische Schriftzüge. Bin aber auch offen für andere Vorschläge.
Dunkelblau, weiß und türkis oder auch rosa mag ich ganz gerne. Wobei Dunkelblau, weiß und türkis meine Favoriten sind und mit rosa höchstens kleinere Akzente gesetzt werden sollten.
Das Buchcover soll modern sein und direkt ansprechen. Gerne eine originelle Lösung, oder etwas Besonderes, etwas das Tiefe ausdrückt, oder man mehrmals hinsehen muss um etwas zu erkennen oder etwas das mehr Interpretationsspielraum lässt.
Gerne auch viel weiß, zumindest heller und nicht zu dunkel. Stylish, aber nicht überfrachtet.
Schreib mich gerne an, wenn du Fragen hast.
Ich habe mal zwei Beispiel von Typolösungen angehängt, die ich ganz cool fände.
Ich freue mich auf deine Ideen :-)
Ganz liebe Grüße
Mira

```html
<!DOCTYPE html>
<html lang="de">
<head>
<meta charset="utf-8">
<title>Morgenlicht NEU entdecken – Dr. Mira Kessow</title>
<link rel="stylesheet" href="https://fonts.googleapis.com/css2?family=Bebas+Neue&family=Roboto:wght@400&family=Yellowtail&display=swap">
<style>
  :root {
    --teal: #50b9a6;
    --gold-light: #d3c145;
    --gold-dark: #a68a1a;
    --paper: #ffffff;
  }
  html, body {
    margin: 0;
    padding: 0;
    width: 750px;
    height: 1200px;
    overflow: hidden;
    background: var(--paper);
  }
  .cover {
    position: relative;
    width: 750px;
    height: 1200px;
    background: var(--paper);
    overflow: hidden;
  }
  .title {
    margin: 0;
    font-weight: 400;
  }
  .author,
  .title-line,
  .subtitle {
    position: absolute;
    left: 0;
    width: 100%;
    margin: 0;
    text-align: center;
    color: var(--teal);
    line-height: 1;
    white-space: nowrap;
  }
  .author {
    top: 74px;
    font-family: "Bebas Neue", "Arial Narrow", sans-serif;
    font-size: 37px;
  }
  .title-line {
    font-family: "Bebas Neue", "Arial Narrow", sans-serif;
    font-weight: 400;
  }
  .title-top {
    top: 140px;
    font-size: 155px;
    letter-spacing: -1px;
  }
  .title-bottom {
    top: 442px;
    font-size: 170px;
  }
  .title-script {
    position: absolute;
    left: 0;
    top: 178px;
    width: 100%;
    text-align: center;
    font-family: "Yellowtail", cursive;
    font-size: 300px;
    line-height: 1;
    text-transform: lowercase;
    white-space: nowrap;
    color: var(--gold-dark);
    background: linear-gradient(120deg, var(--gold-light) 0%, var(--gold-dark) 45%, var(--gold-light) 100%);
    -webkit-background-clip: text;
    background-clip: text;
    -webkit-text-fill-color: transparent;
    transform: rotate(-4deg);
    z-index: 2;
  }
  .subtitle {
    top: 608px;
    font-family: "Roboto", Arial, sans-serif;
    font-size: 35px;
    letter-spacing: 0.5px;
  }
  .ornament {
    position: absolute;
    left: 218px;
    top: 742px;
    width: 318px;
    height: 132px;
    border-radius: 50%;
    background: linear-gradient(100deg, var(--gold-light) 0%, var(--gold-dark) 100%);
    opacity: 0.85;
  }
</style>
</head>
<body>
  <main class="cover">
    <p class="author">Dr. Mira Kessow</p>
    <h1 class="title">
      <span class="title-line title-top">Morgenlicht</span>
      <span class="title-line title-bottom">Entdecken</span>
      <span class="title-script">neu</span>
    </h1>
    <p class="subtitle">Spüre den Mut der ganz in dir wohnt</p>
    <div class="ornament" role="img" aria-label="Goldenes Ornament: Unendlichkeitsschleife mit Herz"></div>
  </main>
</body>
</html>
```